Lotstallmart.com Webpage Design

Design Brief for lotstallmart.com (Copy of Brief also in attached Word file)

Name of Website- lotstallmart.com (existing logo and look & feel of website to be changed)

Logo - Finalised. The logo files are attached with the brief as “logo.jpeg”. The “Blue- Grey” version of the logo is for use on lighter backgrounds and the “Orange-White” version of the logo is for use on darker backgrounds. (A full Black version of the logo is also attached). Both versions may be used in different parts of the website. All attached files are in .png format.
Status - The website in functional and is undergoing user trials. However, we want to improve the look & feel of the website so at it seems
a. cotemporary,
b. Easy to Navigate
c. professional and
d. Vibrant.

Please visit ‘lotstallmart.com’ to check out the website and its functionalities – please use it only as a reference for the features & functions to be provided, however the designer should use a ‘Free Hand’ in designing the composition of various parts of the webpage without getting too influenced by the existing design

Objective of the Website ‘lotstallmart.com –
a. It is a portal focussed on listing of ‘Retail’ specific real-estate properties by developers, owners and realty brokers. The properties shall listed under the following four categories-
i. Retail Malls
ii. Shopping Complexes
iii. High-street shops
iv. Retail Warehouses
*refer lotstallmart.com for better clarity

b. The abovementioned properties shall be listed either for ‘Sale’ or ‘rent\lease’ or both

c. Users shall visit the site in case they wish to acquire a retail \ shop space either on ‘sale’ or ‘rent’. These Users would be able to specify the ‘Search Criteria’ through the tool-bars provided on the website – the ‘Search Criteria’ shall comprise of ‘Type of space category’, ‘City’, ‘Locality’, transaction type ie ‘Rent \ Sale’ and ‘Area Range’

d. The main revenue model for the website shall be listing fee ( or advertising charges ) payable by those listing their properties on the website.

Three Main Pages of Website (lotstallmart.com) that need to be designed -
a. Main Home Page (visit the web link - http://lotstallmart.com/ ) - The main home page has the “Search Toolbar” for specifying of Search Criteria by the User. It shall also have the following features & functions-
i. Main Advertising Banner
ii. Featured Projects
iii. New Launches
iv. Toolbar with buttons – ‘Advertise with Us’, ‘Listings Alert’, ‘Mart Wizards’, ‘Advertiser Login’

b. Property Listings Page (visit the web link - http://lotstallmart.com/gurgaon-in-india ) - The List of property options that match the Criteria specified by the ‘User’ get displayed on this page.

c. Property Detail Page - When the ‘User’ clicks on the “More….” Button on the ‘Property Listings Page’ (given in point b. above) the web page with the details of the property opens. (For Example – visit the web link - http://lotstallmart.com/vorne-Shopping-Complex-vorne-quadrion-gurgaon-636 )

Note:- Please refer to attached ‘Shopping’ related images the designer may use them on the website to provide a look & feel of retail if required – either separately or rotate in a single window

Target Market(s)

Retailers & Investors looking for retail space, Real Estate Brokers, Developers

Industry/Entity Type

Advertising

Number of Pages Required

3 page

Requirements
Must have
• Refer to existing site lotstallmart.com -- all the existing functionalities are a must have.
Nice to have
• The Designer may use the retail related images on the website if required for making it more vibrant. Refer attached images Shopping(1-6).jpg

```html
<!DOCTYPE html>
<html lang="en">
<head>
<meta charset="utf-8">
<title>Lotstallmart.com – Retail Space Portal</title>
<link rel="stylesheet" href="https://fonts.googleapis.com/css2?family=Oxygen:wght@300;400;700&family=Open+Sans:wght@400;600;700&display=swap">
<style>
:root{
  --blue:#1b9ce6;
  --blue-dark:#0f7fc4;
  --orange:#f6a81d;
  --ink:#2b2b2b;
  --text:#444;
  --muted:#8a8a8a;
  --panel:#ebebeb;
  --card:#6f6f6f;
  --white:#fff;
  --dark:#1c1f24;
}
*{box-sizing:border-box;margin:0;padding:0}
html,body{width:1200px;height:4128px;overflow:hidden}
body{font-family:"Open Sans",Arial,sans-serif;color:var(--text);background:var(--white);position:relative}
.abs{position:absolute}
h1,h2,h3{font-family:"Oxygen",Arial,sans-serif;font-weight:400}

/* top city bar */
.city-bar{left:0;top:0;width:1200px;height:22px;background:var(--blue);display:flex;justify-content:center;gap:22px;align-items:center;font-size:10px;font-weight:700;color:var(--white);letter-spacing:.3px;padding-left:120px}
.account-links{right:90px;top:38px;font-size:10px;color:#ddd}

/* hero */
.hero{left:0;top:0;width:1200px;height:633px;background:linear-gradient(180deg,#2e241c 0%,#5a4331 35%,#6b5236 55%,#2c241d 100%);z-index:-1}
.hero-shade{left:0;top:0;width:1200px;height:633px;background:radial-gradient(ellipse at 50% 40%,rgba(255,210,140,.18),rgba(0,0,0,.35) 70%)}
.logo{left:88px;top:46px;display:flex;align-items:center;gap:10px;color:var(--white);font-family:"Oxygen",sans-serif;font-weight:700;font-size:26px}
.logo .dot{width:26px;height:26px;border-radius:50%;background:var(--white)}
.main-nav{left:440px;top:63px;display:flex;gap:6px;align-items:center;font-size:12px;color:var(--white)}
.main-nav a{color:var(--white);text-decoration:none;padding:4px 8px;line-height:14px}
.main-nav .active{background:var(--blue)}
.main-nav .login{background:var(--orange);font-weight:600;margin-left:20px}
.main-nav .register{background:#2f3237;font-weight:600}
.hero-title{left:0;top:252px;width:1200px;text-align:center;color:var(--white);font-size:34px;font-weight:700;font-family:"Oxygen",sans-serif}
.hero-sub{left:0;top:296px;width:1200px;text-align:center;color:#eee;font-size:15px}
.btn-start{left:527px;top:335px;width:146px;height:36px;background:var(--orange);color:var(--white);font-size:14px;font-weight:600;display:flex;align-items:center;justify-content:center;gap:6px}
.how{left:0;top:390px;width:1200px;text-align:center;color:var(--white);font-size:14px}
.dots{left:555px;top:432px;display:flex;gap:6px}
.dots span{width:16px;height:4px;background:rgba(255,255,255,.5)}
.dots span.on{background:var(--white);width:24px}
.format-strip{left:0;top:540px;width:1200px;height:93px;background:rgba(0,0,0,.35)}
.format{top:562px;display:flex;align-items:center;gap:10px;color:var(--white);font-size:13px;line-height:16px}
.format .ring{width:50px;height:50px;border:2px solid rgba(255,255,255,.8);border-radius:50%;display:flex;align-items:center;justify-content:center}

/* search */
.search{left:0;top:633px;width:1200px;height:289px;background:var(--panel)}
.search h2{left:165px;top:690px;font-size:25px;color:var(--ink)}
.meaning{left:510px;top:693px;font-size:11px;color:var(--blue-dark)}
.meaning::before{content:"";position:absolute;left:-18px;top:7px;width:14px;height:1px;background:var(--blue)}
.chk{font-size:11px;color:var(--text);display:flex;align-items:center;gap:8px}
.chk .box{width:18px;height:18px;border:1px solid #aaa;background:var(--white);display:flex;align-items:center;justify-content:center}
.field{height:36px;background:var(--white);border:1px solid #c9c9c9;font-size:11px;color:var(--muted);padding:0 10px;display:flex;align-items:center;justify-content:space-between}
.field.focus{border:2px solid var(--blue);color:var(--blue)}
.btn-search{left:699px;top:842px;width:159px;height:33px;background:var(--orange);color:var(--white);font-size:13px;font-weight:700;display:flex;align-items:center;justify-content:center;gap:6px}

/* intro */
.intro{left:170px;top:970px;width:860px;text-align:center;font-size:14.5px;line-height:21px;color:#333}

/* section titles */
.sec-title{left:0;width:1200px;text-align:center;font-size:33px;color:var(--ink)}
.sec-sub{left:0;width:1200px;text-align:center;font-size:11px;color:var(--muted)}
.sec-sub span{display:inline-flex;align-items:center;gap:12px}
.sec-sub span::before,.sec-sub span::after{content:"";width:50px;height:1px;background:#777}

/* listing grid */
.grid{left:60px;width:1080px;display:grid;grid-template-columns:repeat(4,264px);grid-auto-rows:262px;column-gap:8px;row-gap:12px}
.tile{position:relative;overflow:hidden}
.tile .view{position:absolute;right:8px;top:14px;background:rgba(0,0,0,.55);color:var(--white);font-size:10px;padding:3px 8px}
.tile .tag{position:absolute;left:8px;bottom:6px;color:var(--white);font-size:10px}
.tile .overlay{position:absolute;inset:0;background:rgba(25,45,60,.78);color:var(--white);text-align:center;padding-top:62px}
.overlay h3{font-size:20px;font-weight:700}
.overlay p{font-size:14px;margin-top:4px}
.overlay .loc{font-size:12px;margin-top:18px;color:#ddd}
.overlay .plus{width:26px;height:26px;border:1px solid #fff;border-radius:50%;margin:12px auto 0;display:flex;align-items:center;justify-content:center;font-size:16px}
.overlay .vl{font-size:11px;color:var(--orange);margin-top:10px}

/* wizards band */
.wiz-photo{left:0;top:1844px;width:559px;height:261px;background:linear-gradient(120deg,#2a3a4c,#4c5d70 50%,#1f2a36)}
.wiz-photo-shade{left:0;top:1844px;width:559px;height:261px;background:rgba(0,0,0,.35)}
.wiz-title{left:0;top:1920px;width:559px;text-align:center;color:var(--white);font-size:22px;font-weight:700;font-family:"Oxygen",sans-serif}
.wiz-text{left:120px;top:1955px;width:360px;text-align:center;color:#eee;font-size:13px;line-height:18px}
.wiz-bar{left:318px;top:2028px;width:20px;height:3px;background:var(--white)}
.wiz-form{left:559px;top:1844px;width:641px;height:261px;background:var(--blue)}
.in{background:var(--white);font-size:11px;color:var(--muted);padding:0 10px;display:flex;align-items:center}
.btn-send{left:594px;top:2028px;width:94px;height:33px;border:1px solid var(--white);color:var(--white);font-size:13px;display:flex;align-items:center;justify-content:center;gap:6px}

/* alert + editor */
.card{top:2920px;height:492px;background:var(--card);color:var(--white)}
.card h3{position:absolute;left:0;top:42px;width:100%;text-align:center;font-size:21px}
.card .txt{position:absolute;text-align:center;font-size:11px;line-height:14px}
.card .hint{position:absolute;font-size:8px;color:#cfcfcf}
.btn-ghost{position:absolute;height:34px;border:1px solid var(--white);font-size:13px;display:flex;align-items:center;justify-content:center;gap:8px}

/* footer */
.footer{left:0;top:3500px;width:1200px;height:628px;background:linear-gradient(180deg,#3a3d42 0%,#55575b 45%,#2c2d30 100%)}
.footer-shade{left:0;top:3500px;width:1200px;height:628px;background:rgba(10,12,15,.45)}
.f-logo{left:0;top:3596px;width:1200px;display:flex;justify-content:center;align-items:center;gap:8px;color:var(--white);font-family:"Oxygen",sans-serif;font-weight:700;font-size:20px}
.f-logo .dot{width:20px;height:20px;border-radius:50%;background:var(--white)}
.f-rule{top:3627px;height:1px;width:130px;background:rgba(255,255,255,.6)}
.f-links{left:0;width:1200px;display:flex;justify-content:center;gap:22px;font-size:11px;color:var(--white)}
.f-links .cur{color:var(--orange)}
.thumbs{left:324px;top:3792px;display:flex;gap:15px}
.thumbs div{width:75px;text-align:center;font-size:8px;color:#ddd}
.thumbs i{display:block;height:52px;border:2px solid var(--white);margin-bottom:4px}
.f-addr{left:96px;top:3968px;display:flex;gap:12px;color:var(--white);font-size:11px;line-height:16px}
.social{left:590px;top:3972px;display:flex;gap:12px}
.social span{width:16px;height:16px;border-radius:50%;background:var(--white)}
.copy{right:88px;top:3968px;text-align:right;color:var(--white);font-size:11px;line-height:16px}
</style>
</head>
<body>

<!-- HERO -->
<div class="abs hero" role="img" aria-label="Photo of a family shopping with bags in a lit arcade"></div>
<div class="abs hero-shade"></div>
<div class="abs city-bar">
  <span>BANGALORE</span><span>CHENNAI</span><span>GREATER NOIDA</span><span>GURGAON</span><span>HYDERABAD</span><span>JAIPUR</span><span>KHANNA</span><span>KOLKATA</span><span>MUMBAI</span><span>NOIDA</span><span>PUNE</span><span>SURAT</span>
</div>
<div class="abs account-links">Login | Forgot Password</div>
<div class="abs logo"><span class="dot"></span>lotstallmart</div>
<nav class="abs main-nav">
  <a class="active">Home</a><a>Advertise with Us</a><a>Mart Wizards</a><a>Listing Alert</a>
  <a class="login">Advertiser Login</a><a class="register">&#8250; New Advertiser - Register</a>
</nav>
<h1 class="abs hero-title">Shops at Cox Town Bangalore</h1>
<p class="abs hero-sub">Lorem ipsum dolor sit amet, consectetur adipiscing elit</p>
<div class="abs btn-start">Get Started <span>&#8250;</span></div>
<div class="abs how">&#9656; How it Work</div>
<div class="abs dots"><span class="on"></span><span></span><span></span></div>

<div class="abs format-strip"></div>
<div class="abs format" style="left:220px"><span class="ring"><svg width="24" height="24" viewBox="0 0 24 24" fill="none" stroke="#fff" stroke-width="1.6"><path d="M3 9h18l-2-5H5z"/><path d="M5 9v11h14V9"/><path d="M10 20v-6h4v6"/></svg></span><span>Retail<br>Malls</span></div>
<div class="abs format" style="left:400px"><span class="ring"><svg width="24" height="24" viewBox="0 0 24 24" fill="none" stroke="#fff" stroke-width="1.6"><path d="M6 8h12l1 13H5z"/><path d="M9 8a3 3 0 0 1 6 0"/></svg></span><span>Shopping<br>Complexes</span></div>
<div class="abs format" style="left:614px"><span class="ring"><svg width="24" height="24" viewBox="0 0 24 24" fill="none" stroke="#fff" stroke-width="1.6"><rect x="4" y="4" width="16" height="16"/><path d="M4 10h16M12 10v10"/></svg></span><span>High-Street<br>Shops</span></div>
<div class="abs format" style="left:812px"><span class="ring"><svg width="24" height="24" viewBox="0 0 24 24" fill="none" stroke="#fff" stroke-width="1.6"><path d="M3 10l9-6 9 6v10H3z"/><path d="M7 20v-7h10v7M7 16h10"/></svg></span><span>Retail<br>Warehouses</span></div>

<!-- SEARCH -->
<section class="abs search"></section>
<h2 class="abs" style="left:165px;top:688px;font-size:25px;color:var(--ink)">Select Retail Format</h2>
<div class="abs meaning">Meaning of Retail Format</div>
<div class="abs chk" style="left:165px;top:745px"><span class="box"><svg width="12" height="12" viewBox="0 0 12 12"><path d="M2 6l3 3 5-7" fill="none" stroke="#222" stroke-width="2"/></svg></span>Retail Malls</div>
<div class="abs chk" style="left:337px;top:745px"><span class="box"></span>Retail Warehouses</div>
<div class="abs chk" style="left:165px;top:786px"><span class="box"></span>Shopping Complex</div>
<div class="abs chk" style="left:337px;top:786px"><span class="box"></span>High Street Shops</div>
<div class="abs field focus" style="left:528px;top:743px;width:256px">Enter Keywords</div>
<div class="abs field" style="left:801px;top:743px;width:256px">Select City <span>&#9662;</span></div>
<div class="abs field" style="left:528px;top:787px;width:256px">Sale Or Rent Or Both <span>&#9662;</span></div>
<div class="abs field" style="left:801px;top:787px;width:256px">Select Locality/Micro-Market <span>&#9662;</span></div>
<div class="abs btn-search"><svg width="13" height="13" viewBox="0 0 14 14" fill="none" stroke="#fff" stroke-width="2"><circle cx="6" cy="6" r="4.5"/><path d="M9.5 9.5L13 13"/></svg>SEARCH</div>

<p class="abs intro">Lotstallmart.com is a Specialised Web based platform for Retail Space, featuring properties across India under various formats such as Retail Malls, Shopping Complexes, High-street Shops. Also featured are Retail Warehouses which provide the logistic back-end for the retail business. Lotstallmart.com is useful to various category of users as follows- a. Devel</p>

<!-- FEATURED PROJECTS -->
<h2 class="abs sec-title" style="top:1113px">Featured Retail Projects</h2>
<div class="abs sec-sub" style="top:1171px"><span>Across India</span></div>
<div class="abs grid" style="top:1219px">
  <div class="tile" role="img" aria-label="Photo of a shopping complex tower" style="background:linear-gradient(160deg,#6d7f93,#2f3d4c)">
    <div class="overlay"><h3>Mallorn</h3><p>Shopping Complex</p><div class="loc">&#9679; Surat - Althan</div><div class="plus">+</div><div class="vl">View the Listing</div></div>
  </div>
  <div class="tile" role="img" aria-label="Photo of a lit mall at dusk" style="background:linear-gradient(180deg,#3b5a86,#a5865c)"><span class="view">View the Listing</span></div>
  <div class="tile" role="img" aria-label="Photo of a tall commercial tower against blue sky" style="background:linear-gradient(180deg,#2e78c7,#c6a35c)"><span class="view">View the Listing</span></div>
  <div class="tile" role="img" aria-label="Photo of a glass atrium mall" style="background:linear-gradient(180deg,#cfe3f0,#7a9aac)"><span class="view">View the Listing</span></div>
  <div class="tile" role="img" aria-label="Photo of a glass shopfront with signage" style="background:linear-gradient(180deg,#b8d4e6,#4b6a80)"><span class="view">View the Listing</span></div>
  <div class="tile" role="img" aria-label="Photo of a red and white mall facade" style="background:linear-gradient(180deg,#9ec6e8,#b9443f)"><span class="view">View the Listing</span></div>
  <div class="tile" role="img" aria-label="Photo of a mall facade with large billboards" style="background:linear-gradient(180deg,#8fa9c2,#6b6056)"><span class="view">View the Listing</span><span class="tag">- 81, Gurgaon</span></div>
  <div class="tile" role="img" aria-label="Rendering of a modern retail building" style="background:linear-gradient(180deg,#c7d7e6,#4e6f86)"><span class="view">View the Listing</span></div>
</div>

<!-- MART WIZARDS -->
<div class="abs wiz-photo" role="img" aria-label="Photo of city office towers"></div>
<div class="abs wiz-photo-shade"></div>
<h3 class="abs wiz-title">Mart Wizards</h3>
<p class="abs wiz-text">Post your Retail Space requirement with us and our experts shall get back with suitable options and even help you in your transaction. This is a Free Service!</p>
<div class="abs wiz-bar"></div>
<div class="abs wiz-form"></div>
<div class="abs in" style="left:594px;top:1896px;width:254px;height:33px">Enter Email</div>
<div class="abs in" style="left:856px;top:1896px;width:253px;height:33px">Mobile</div>
<div class="abs in" style="left:594px;top:1943px;width:515px;height:74px;align-items:flex-start;padding-top:10px">Message</div>
<div class="abs btn-send">Send <span>&#8250;</span></div>

<!-- NEW LAUNCHES -->
<h2 class="abs sec-title" style="top:2183px">Featured New Launches</h2>
<div class="abs sec-sub" style="top:2241px"><span>Across India</span></div>
<div class="abs grid" style="top:2306px">
  <div class="tile" role="img" aria-label="Photo of a mall interior atrium" style="background:linear-gradient(180deg,#8f8d87,#4a4a4a)"><span class="view">View the Listing</span></div>
  <div class="tile" role="img" aria-label="Photo of a mall interior with shops" style="background:linear-gradient(180deg,#6e4b32,#b88a5a)"><span class="view">View the Listing</span></div>
  <div class="tile" role="img" aria-label="Rendering of a retail plaza" style="background:linear-gradient(180deg,#aad0ee,#9c8a76)"><span class="view">View the Listing</span></div>
  <div class="tile" role="img" aria-label="Rendering of a shopping complex" style="background:linear-gradient(180deg,#7fb6e4,#a36f55)"><span class="view">View the Listing</span></div>
  <div class="tile" role="img" aria-label="Photo of a glass shopfront with signage" style="background:linear-gradient(180deg,#b8d4e6,#4b6a80)"><span class="view">View the Listing</span></div>
  <div class="tile" role="img" aria-label="Photo of a red and white mall facade" style="background:linear-gradient(180deg,#9ec6e8,#b9443f)"><span class="view">View the Listing</span></div>
  <div class="tile" role="img" aria-label="Photo of a mall facade with large billboards" style="background:linear-gradient(180deg,#8fa9c2,#6b6056)"><span class="view">View the Listing</span><span class="tag">- 81, Gurgaon</span></div>
  <div class="tile" role="img" aria-label="Rendering of a modern retail building" style="background:linear-gradient(180deg,#c7d7e6,#4e6f86)"><span class="view">View the Listing</span></div>
</div>

<!-- LISTING ALERT -->
<section class="abs card" style="left:259px;width:335px">
  <h3>&mdash; Listing Alert &mdash;</h3>
  <p class="txt" style="left:30px;top:103px;width:275px">Subscribe for Fortnightly Email update on New Listings @ Lotstallmart</p>
  <div class="field focus" style="position:absolute;left:44px;top:165px;width:256px;height:33px">Enter Email</div>
  <div class="field" style="position:absolute;left:44px;top:214px;width:256px;height:33px">Select Question <span>&#9662;</span></div>
  <span class="hint" style="left:44px;top:252px">Select your category</span>
  <div class="field" style="position:absolute;left:44px;top:289px;width:256px;height:33px">Select City <span>&#9662;</span></div>
  <span class="hint" style="left:44px;top:327px">Select cities of interest</span>
  <div class="btn-ghost" style="left:79px;top:390px;width:152px">Subscribe <span>&#8250;</span></div>
</section>

<!-- EDITOR'S CHOICE -->
<section class="abs card" style="left:603px;width:341px">
  <h3>&mdash; Editor's Choice &mdash;</h3>
  <div role="img" aria-label="Photo of a white commercial building against blue sky" style="position:absolute;left:33px;top:107px;width:203px;height:165px;background:linear-gradient(180deg,#2f73c4,#cfd8e2)"></div>
  <p class="txt" style="left:26px;top:286px;width:289px">A "Select" Listing of Retail Properties Handpicked by our Editors based on their own positive evaluation on parameters &amp; attributes such as Design Concept, Location, Developer, Success Potential. So Read On to Check Out for yourself...</p>
  <div class="btn-ghost" style="left:110px;top:390px;width:102px">More <span>&#8250;</span></div>
</section>

<!-- FOOTER -->
<div class="abs footer" role="img" aria-label="Photo of a family walking down a shopping street"></div>
<div class="abs footer-shade"></div>
<div class="abs f-rule" style="left:407px"></div>
<div class="abs f-rule" style="left:663px"></div>
<div class="abs f-logo"><span class="dot"></span>lotstallmart</div>
<div class="abs f-links" style="top:3708px"><span class="cur">About Us</span><span>Privacy Policy</span><span>Terms of Use</span><span>Contact Us</span><span>Site Map</span></div>
<div class="abs f-links" style="top:3741px"><span>Retail Malls</span><span>Shopping Complex</span><span>High Street Shops</span><span>Retail Warehouses</span></div>
<div class="abs thumbs">
  <div><i role="img" aria-label="Mall thumbnail" style="background:#7a93b0"></i>Lorem ipsum</div>
  <div><i role="img" aria-label="Mall thumbnail" style="background:#9a7d63"></i>Lorem ipsum</div>
  <div><i role="img" aria-label="Mall thumbnail" style="background:#a9545a"></i>Lorem ipsum</div>
  <div><i role="img" aria-label="Mall thumbnail" style="background:#8aa2b8"></i>Lorem ipsum</div>
  <div><i role="img" aria-label="Mall thumbnail" style="background:#6f86a0"></i>Lorem ipsum</div>
  <div><i role="img" aria-label="Mall thumbnail" style="background:#a3b6c8"></i>Lorem ipsum</div>
</div>
<div class="abs f-addr">
  <svg width="22" height="30" viewBox="0 0 22 30"><path d="M11 1a10 10 0 0 0-10 10c0 8 10 18 10 18s10-10 10-18A10 10 0 0 0 11 1z" fill="#fff"/><circle cx="11" cy="11" r="4" fill="#3a3d42"/></svg>
  <div>Unit 406, 4th Floor, Lorem ipsum is simply, Sector x, Gurgaon - 122002<br>P : 000-000-0000 &nbsp;&nbsp; F : 000-000-0000</div>
</div>
<div class="abs social" aria-label="Social links"><span></span><span></span><span></span><span></span></div>
<div class="abs copy">Copyright &copy; 2015 Retail Portal Hub.com<br>All rights reserved</div>

</body>
</html>
```